Letterhead and matching envelope design for a dental office

We need a new stationary design, letterhead and envelope #10, for a dental office in Denver area. We are called Bright Harbor Dental. We want a simple and minimalistic design but not a boring design. I wish to have one good point that makes it look professional. I have attached our logo. Feel free to use either one. I want the design for letterhead and envelope look like a "matching pair" but not look the same. The envelope doesn't have to be white and it will have an address window on bottom left.

Target Market(s)

everyone who visits dentist (adults)

Industry/Entity Type

Dental

Font styles to use
Other font styles liked:
• close to font on logo or something that matches well

Requirements
Must have
• professional
• simple, minimalistic
• unique point that stands out
Nice to have
• matching but not same design for letterhead and envelope
Should not have
• not look like all the other boring designs
• no flowery, distracting feats

```html
<!DOCTYPE html>
<html lang="en">
<head>
<meta charset="utf-8">
<title>Bright Harbor Dental – Letterhead</title>
<link rel="stylesheet" href="https://fonts.googleapis.com/css2?family=Arimo:wght@400;700&display=swap">
<style>
  :root {
    --backdrop: #ececec;
    --paper: #ffffff;
    --green: #2fae3f;
    --green-soft: #b9dfb6;
    --ink: #2a2a2a;
    --body: #555555;
    --sign-tone: #dcdcdc;
  }
  * { box-sizing: border-box; margin: 0; padding: 0; }
  html, body {
    width: 1200px; height: 795px; overflow: hidden;
    background: var(--backdrop);
    font-family: "Arimo", Arial, sans-serif;
  }
  .letterhead {
    position: absolute; left: 330px; top: 16px;
    width: 540px; height: 764px;
    background: var(--paper);
    box-shadow: 0 2px 10px rgba(0,0,0,.12);
    overflow: hidden;
  }
  .swoosh { position: absolute; left: 0; top: 0; width: 540px; height: 270px; }
  .brand {
    position: absolute; top: 40px; right: 96px;
    display: flex; align-items: center; gap: 8px;
    white-space: nowrap;
  }
  .brand-dot { width: 12px; height: 12px; border-radius: 50%; background: var(--green); }
  .brand-name { color: var(--green); font-weight: 700; font-size: 15px; letter-spacing: .5px; }
  .letter { position: absolute; left: 46px; top: 282px; width: 420px; color: var(--body); font-size: 10.5px; line-height: 1.45; }
  .salutation { color: var(--ink); font-weight: 700; font-size: 12px; margin-bottom: 8px; }
  .letter p { margin-bottom: 12px; }
  .signature {
    position: absolute; left: 46px; top: 560px;
    width: 110px; height: 38px; background: var(--sign-tone); border-radius: 3px;
  }
  .footer { position: absolute; right: 34px; bottom: 36px; text-align: right; color: var(--ink); font-size: 9.5px; line-height: 1.6; }
  .footer-name { color: var(--green); font-weight: 700; font-size: 10px; }
  .contacts { display: flex; justify-content: flex-end; gap: 8px; align-items: center; }
  .contact { display: inline-flex; align-items: center; gap: 3px; }
  .contact svg { width: 10px; height: 10px; }
  .rule { position: absolute; left: 0; right: 0; bottom: 22px; height: 4px; background: var(--green); }
</style>
</head>
<body>
  <main class="letterhead">
    <svg class="swoosh" viewBox="0 0 540 270" aria-hidden="true">
      <path fill="var(--green-soft)" d="M0 236 C120 196 230 192 330 150 C226 208 100 224 0 266 Z"/>
      <path fill="var(--green)" d="M0 214 C150 150 300 170 420 110 C470 85 500 40 510 0 L526 0 C516 46 484 96 430 126 C310 188 150 180 0 234 Z"/>
    </svg>

    <div class="brand">
      <span class="brand-dot"></span>
      <span class="brand-name">Bright Harbor Dental</span>
    </div>

    <section class="letter">
      <div class="salutation">Dear Mr. Carter,</div>
      <p>Lorem Ipsum is simply dummy text of the printing and typesetting industry. Lorem Ipsum has been the industry's standard dummy text ever since the 1500s, when an unknown printer took a galley of type and scrambled it to make a type specimen book. It has survived not only five centuries, but also the leap into electronic typesetting, remaining essentially unchanged.</p>
      <p>The standard chunk of Lorem Ipsum used since the 1500s is reproduced below for those interested. Sections 1.10.32 and 1.10.33 from "de Finibus Bonorum et Malorum" by Cicero are also reproduced in their exact original form, accompanied by English versions from the 1914 translation by H. Rackham.</p>
      <p>Lorem Ipsum is simply dummy text of the printing and typesetting industry. Lorem Ipsum has been the industry's standard dummy text ever since the 1500s, when an unknown printer took a galley of type and scrambled it to make a type specimen book. It has survived not only five centuries, but also the leap into electronic typesetting, remaining essentially unchanged. It was popularised in the</p>
    </section>

    <div class="signature" role="img" aria-label="Handwritten signature"></div>

    <footer class="footer">
      <div class="footer-name">Bright Harbor Dental</div>
      <div>2285 LAKEVIEW DR, SUITE 210 ARVADA, CO 80004</div>
      <div class="contacts">
        <span class="contact">
          <svg viewBox="0 0 10 10" aria-hidden="true"><circle cx="5" cy="5" r="5" fill="var(--green)"/><path d="M3.2 2.6l1 .9-.5.7c.4.8.9 1.3 1.6 1.6l.7-.5.9 1-.7.8C4.6 7 3 5.4 2.7 3.3z" fill="#fff"/></svg>
          720-555-0148
        </span>
        <span class="contact">
          <svg viewBox="0 0 10 10" aria-hidden="true"><circle cx="5" cy="5" r="5" fill="var(--green)"/><rect x="2.6" y="3.3" width="4.8" height="3.4" fill="#fff"/><path d="M2.6 3.3L5 5.2 7.4 3.3" stroke="var(--green)" stroke-width=".6" fill="none"/></svg>
          info@brightharbordental.com
        </span>
        <span class="contact">
          <svg viewBox="0 0 10 10" aria-hidden="true"><circle cx="5" cy="5" r="5" fill="var(--green)"/><circle cx="5" cy="5" r="2.6" stroke="#fff" stroke-width=".7" fill="none"/><path d="M2.4 5h5.2M5 2.4v5.2" stroke="#fff" stroke-width=".6"/></svg>
          www.brightharbordental.com
        </span>
      </div>
    </footer>

    <div class="rule"></div>
  </main>
</body>
</html>
```